Kelvaro.ch is looking for business card letterhead and envelope C5 with WOW effect

We need a strong business card for our company Kelvaro.ch, logo is available. You want a black or dark background on which the logo Stark r% 26 # 252; appears. Letterhead and envelope in C5 format should be in a similar design, but does not have to be We need a strong business card for our company Kelvaro.ch, logo is available. A black or dark background is desired, on which the logo Stark comes across. The letterhead and the envelope in C5 format should have a similar design.

Target Market(s)

Private customers as well as entrepreneurs

Contact Information for Business Card

E-mail: info@kelvaro-example.ch
Web.www.Kelvaro-example.ch
Tel: +41 ( 0 ) 79 482 6037
Adresse:
Lindenweg 14
9406 Tarnbach

Hier kann man Icons verwenden für Email,Tel und Adressse

Font styles to use
Other font styles liked:
• Dubai,bold

Colors

Designer to choose colors to be used in the design.

Requirements
Must have
• WOW effect
Nice to have
• R% 26 # 252; back business card with our service listings. - VEHICLE LABELING - SHOP WINDOW LABELING - STICKERS AND MUCH MORE ... in red color

```html
<!DOCTYPE html>
<html lang="en">
<head>
<meta charset="utf-8">
<title>Kelvaro.ch – Business Card</title>
<link rel="stylesheet" href="https://fonts.googleapis.com/css2?family=Open+Sans:wght@400;600;700;800&display=swap">
<style>
  :root {
    --bg: #2a2a2c;
    --card: #16213d;
    --card-light: #1f2d52;
    --white: #ffffff;
    --yellow: #f7c623;
    --red: #d4202b;
  }
  * { box-sizing: border-box; margin: 0; padding: 0; }
  html, body {
    width: 1200px; height: 930px; overflow: hidden;
    background: var(--bg);
    font-family: "Open Sans", sans-serif;
  }
  .stage { position: relative; width: 1200px; height: 930px; }
  .card {
    position: absolute;
    width: 560px; height: 340px;
    border-radius: 22px;
    background: linear-gradient(120deg, var(--card) 0%, var(--card-light) 45%, var(--card) 75%);
    box-shadow: 0 18px 40px rgba(0,0,0,.45);
    color: var(--white);
  }
  .card-front { left: 80px; top: 90px; }
  .card-back { left: 560px; top: 500px; }

  .brand {
    display: flex; align-items: center; gap: 12px;
    font-weight: 800; letter-spacing: 1px; text-transform: uppercase;
  }
  .brand-dot { width: 18px; height: 18px; border-radius: 50%; background: var(--yellow); }

  .card-front .brand { position: absolute; left: 110px; top: 110px; font-size: 40px; }
  .card-front .brand-dot { width: 26px; height: 26px; }
  .services {
    position: absolute; left: 150px; top: 180px;
    list-style: none; text-transform: uppercase;
    font-size: 15px; line-height: 1.45; text-align: right; width: 330px;
  }
  .services li::after {
    content: ""; display: inline-block; width: 8px; height: 8px;
    margin-left: 10px; border: 2px solid var(--red); border-radius: 50%;
    vertical-align: 1px;
  }

  .card-back .brand { position: absolute; left: 50px; top: 148px; font-size: 28px; }
  .divider { position: absolute; left: 300px; top: 70px; width: 2px; height: 200px; background: var(--yellow); }
  .contact { position: absolute; left: 325px; top: 68px; }
  .person-name { font-size: 20px; font-weight: 800; text-transform: uppercase; }
  .person-name .surname { color: var(--yellow); }
  .person-role { font-size: 15px; margin-bottom: 10px; }
  .address { font-size: 15px; line-height: 1.4; margin-bottom: 8px; font-style: normal; }
  .contact-list { list-style: none; font-size: 15px; line-height: 1.55; }
  .contact-list li { display: flex; align-items: center; gap: 10px; }
  .contact-list svg { width: 14px; height: 14px; flex: none; }
</style>
</head>
<body>
<main class="stage">
  <section class="card card-front" aria-label="Card front">
    <div class="brand"><span class="brand-dot"></span>Kelvaro.ch</div>
    <ul class="services">
      <li>Vehicle labeling</li>
      <li>Shop window labeling</li>
      <li>Stickers and much more</li>
    </ul>
  </section>

  <section class="card card-back" aria-label="Card back">
    <div class="brand"><span class="brand-dot"></span>Kelvaro.ch</div>
    <div class="divider"></div>
    <div class="contact">
      <p class="person-name">Lukas <span class="surname">Brenner</span></p>
      <p class="person-role">Director</p>
      <address class="address">Lindenweg 14<br>9406 Tarnbach</address>
      <ul class="contact-list">
        <li>
          <svg viewBox="0 0 24 24" fill="var(--yellow)"><path d="M6.6 10.8a15 15 0 0 0 6.6 6.6l2.2-2.2a1 1 0 0 1 1-.25 11.4 11.4 0 0 0 3.6.57 1 1 0 0 1 1 1V20a1 1 0 0 1-1 1A17 17 0 0 1 3 4a1 1 0 0 1 1-1h3.5a1 1 0 0 1 1 1c0 1.25.2 2.45.57 3.57a1 1 0 0 1-.25 1z"/></svg>
          +41(0)79 482 6037
        </li>
        <li>
          <svg viewBox="0 0 24 24" fill="none" stroke="var(--yellow)" stroke-width="2"><rect x="3" y="5" width="18" height="14" rx="1"/><path d="M3 6l9 7 9-7"/></svg>
          info@kelvaro-example.ch
        </li>
        <li>
          <svg viewBox="0 0 24 24" fill="none" stroke="var(--yellow)" stroke-width="2"><circle cx="12" cy="12" r="9"/><path d="M3 12h18M12 3c3 3 3 15 0 18M12 3c-3 3-3 15 0 18"/></svg>
          www.kelvaro-example.ch
        </li>
      </ul>
    </div>
  </section>
</main>
</body>
</html>
```